Modern Verdell Tree Care Website

I need a website for a full service Tree Care company. The company provides tree pruning, tree removal, tree preservation, emergency services, stump grinding, and emergency tree services.

Target Market(s)

Customers that need tree services

Industry/Entity Type

Landscaping, Tree Services

Coding

Coded - Design and coding required

Number of Pages Required

5+ page

Font styles to use
Sans Serif

Requirements
Must have
• Good clean design that showcases the services the company provides.
Nice to have
• Services page; contact form, blog, home page, about page

```html
<!DOCTYPE html>
<html lang="en">
<head>
<meta charset="utf-8">
<title>Verdell Tree Care</title>
<link rel="stylesheet" href="https://fonts.googleapis.com/css2?family=Michroma&family=Oswald:wght@500;600&family=Poppins:wght@400;500;600&display=swap">
<style>
:root{
  --green:#7cc242;
  --orange:#f7a928;
  --slate:#4b5560;
  --ink:#2c2c2c;
  --card:#f2f2f2;
  --panel:rgba(96,104,108,.82);
  --footer:#3c4347;
  --white:#fff;
}
*{box-sizing:border-box;margin:0;padding:0}
html,body{width:1200px;height:4615px;overflow:hidden}
body{position:relative;font-family:"Poppins",sans-serif;color:var(--ink);background:var(--white)}
.abs{position:absolute}
.btn{position:absolute;display:flex;align-items:center;justify-content:center;font-family:"Poppins",sans-serif;font-size:12px;color:var(--white);background:var(--green)}
.btn-orange{background:var(--orange);color:var(--ink)}
.section-title{position:absolute;left:0;width:1200px;text-align:center;font-family:"Michroma",sans-serif;font-size:32px;letter-spacing:2px;color:var(--slate);line-height:1}
.ornament{position:absolute;width:80px;height:14px}
.photo{position:absolute}

/* header */
.site-header{position:absolute;left:0;top:0;width:1200px;height:98px;background:var(--white)}
.brand{position:absolute;left:141px;top:28px;display:flex;align-items:center;gap:12px}
.brand-mark{width:40px;height:40px;background:var(--green)}
.brand-name{font-family:"Poppins",sans-serif;font-weight:600;font-size:22px;line-height:1.05;color:var(--slate);letter-spacing:1px}
.main-nav{position:absolute;top:38px;font-size:14px;color:var(--ink)}

/* hero */
.hero{position:absolute;left:0;top:98px;width:1200px;height:540px;overflow:hidden}
.hero-bg{position:absolute;inset:0;background:linear-gradient(100deg,#1f6fc4 0%,#2f86d8 45%,#5a9fd8 70%,#3d6f4a 100%)}
.hero-photo{left:600px;top:0;width:360px;height:470px;background:linear-gradient(180deg,#4a8fd0,#33543a 80%)}
.hero-title{position:absolute;left:141px;top:104px;font-family:"Oswald",sans-serif;font-weight:600;font-size:48px;line-height:57px;color:var(--white);letter-spacing:.5px}
.hero-sub{position:absolute;left:141px;top:280px;font-size:21px;font-weight:500;color:var(--white)}
.hero-wave{position:absolute;left:0;top:380px}

/* services */
.services-text{position:absolute;left:250px;width:700px;top:818px;text-align:center;font-size:16px;line-height:27px}
.service-card{position:absolute;top:906px;width:212px;height:246px;background:var(--card)}
.service-card .photo{left:0;top:0;width:212px;height:165px}
.service-icon{position:absolute;left:81px;top:139px;width:50px;height:50px;border-radius:50%;background:var(--green);border:3px solid var(--white);display:flex;align-items:center;justify-content:center}
.service-name{position:absolute;left:0;width:212px;top:1010px;text-align:center;font-size:18px}
.service-card.is-active{background:var(--green)}
.service-card.is-active .service-icon{background:var(--orange)}
.service-card.is-active .service-name{color:var(--white)}
.slider-arrow{position:absolute;top:1080px;width:36px;height:36px;border-radius:50%}

/* about */
.about-photo{left:0;top:1307px;width:1200px;height:593px;background:linear-gradient(90deg,#4a3b2a 0%,#6b5d45 35%,#5f6a4a 60%,#3e4a33 100%)}
.info-panel{position:absolute;background:var(--panel)}
.panel-title{font-family:"Michroma",sans-serif;font-size:31px;line-height:39px;color:var(--white);letter-spacing:2px}
.about-copy{position:absolute;left:32px;top:160px;width:390px;font-size:11.5px;line-height:20px;color:var(--white)}
.about-copy p+p{margin-top:6px}

/* service area */
.area-map{left:143px;top:1984px;width:412px;height:437px;background:radial-gradient(ellipse at 45% 50%,#3c6b2c 0%,#2f5222 55%,#e8eee2 56%,#fff 70%)}
.area-list{position:absolute;font-size:15px;line-height:1}
.area-item{position:absolute;display:flex;align-items:center;gap:18px;white-space:nowrap}
.area-item.is-current{font-weight:600}

/* why */
.why-photo{left:0;top:2507px;width:1200px;height:522px;background:linear-gradient(90deg,#53694a 0%,#8ba47f 35%,#a9c3d6 60%,#6f8a5e 100%)}
.why-item{position:absolute;display:flex;align-items:center;gap:8px;font-size:14px;color:var(--white);white-space:nowrap}

/* blog */
.blog-card{position:absolute;top:3199px;width:283px;height:365px;background:var(--card)}
.blog-card .photo{left:0;top:0;width:283px;height:190px}
.blog-card h3{position:absolute;left:14px;top:210px;width:255px;font-size:13.5px;font-weight:500;line-height:19px}
.blog-card p{position:absolute;left:14px;top:260px;width:255px;font-size:11px;line-height:21px}
.date{position:absolute;display:flex;align-items:center;gap:8px;font-size:10.5px}
.blog-mini{position:absolute;left:747px;width:320px;height:86px}
.blog-mini .photo{left:0;top:0;width:113px;height:86px}
.blog-mini h4{position:absolute;left:127px;top:0;width:190px;font-size:13.5px;font-weight:500;line-height:18px}
.blog-mini .date{left:127px;top:66px}

/* inquiry */
.inquiry-photo{left:0;top:3713px;width:1200px;height:567px;background:linear-gradient(180deg,#5e7a3a 0%,#7d9e4a 40%,#a8b870 70%,#4c6a30 100%)}
.field{position:absolute;background:var(--white);font-size:12px;padding:10px 16px;color:var(--ink)}
.field sup{color:#d0312d;font-size:12px;vertical-align:top;position:relative;top:-1px}

/* footer */
.site-footer{position:absolute;left:0;top:4280px;width:1200px;height:335px;background:var(--footer);color:var(--white)}
.footer-brand{position:absolute;left:141px;top:88px;display:flex;align-items:center;gap:14px}
.footer-brand .brand-mark{width:48px;height:48px}
.footer-brand .brand-name{color:var(--white);font-size:27px}
.social{position:absolute;top:170px;width:36px;height:36px;border-radius:50%;border:1.5px solid var(--white)}
.footer-heading{position:absolute;top:52px;font-size:17px;font-weight:500}
.footer-link{position:absolute;left:582px;font-size:13px}
.contact-row{position:absolute;left:878px;display:flex;gap:14px;font-size:12px;line-height:18px}
.footer-rule{position:absolute;left:141px;top:283px;width:917px;height:1px;background:rgba(255,255,255,.2)}
.copyright{position:absolute;left:0;width:1200px;top:302px;text-align:center;font-size:11px}
</style>
</head>
<body>

<svg width="0" height="0" style="position:absolute">
  <defs>
    <symbol id="ornament" viewBox="0 0 80 14">
      <line x1="0" y1="7" x2="30" y2="7" stroke="#f7a928" stroke-width="2"/>
      <line x1="50" y1="7" x2="80" y2="7" stroke="#f7a928" stroke-width="2"/>
      <circle cx="40" cy="7" r="6" fill="none" stroke="#7cc242" stroke-width="1.5"/>
      <circle cx="40" cy="7" r="2.5" fill="#7cc242"/>
    </symbol>
    <symbol id="pin" viewBox="0 0 14 18">
      <path d="M7 0C3.1 0 0 3.1 0 7c0 5 7 11 7 11s7-6 7-11c0-3.9-3.1-7-7-7z" fill="currentColor"/>
      <circle cx="7" cy="7" r="2.6" fill="#fff"/>
    </symbol>
    <symbol id="tick" viewBox="0 0 16 16">
      <circle cx="8" cy="8" r="7" fill="none" stroke="#f7a928" stroke-width="1.5"/>
      <path d="M4.5 8.2l2.4 2.4 4.6-4.8" fill="none" stroke="#f7a928" stroke-width="1.5"/>
    </symbol>
    <symbol id="calendar" viewBox="0 0 14 14">
      <rect x="1" y="2.5" width="12" height="10.5" fill="none" stroke="#7cc242" stroke-width="1.3"/>
      <line x1="1" y1="5.5" x2="13" y2="5.5" stroke="#7cc242" stroke-width="1.3"/>
      <line x1="4" y1="1" x2="4" y2="4" stroke="#7cc242" stroke-width="1.3"/>
      <line x1="10" y1="1" x2="10" y2="4" stroke="#7cc242" stroke-width="1.3"/>
    </symbol>
    <symbol id="tree" viewBox="0 0 24 24">
      <path d="M12 2L5 13h4l-3 5h12l-3-5h4z" fill="#fff"/>
      <rect x="11" y="18" width="2" height="4" fill="#fff"/>
    </symbol>
  </defs>
</svg>

<!-- Header -->
<header class="site-header">
  <div class="brand">
    <span class="brand-mark"></span>
    <span class="brand-name">VERDELL<br>TREE CARE</span>
  </div>
  <nav>
    <span class="main-nav" style="left:582px">Home</span>
    <span class="main-nav" style="left:666px">About Us</span>
    <span class="main-nav" style="left:772px">Services</span>
    <span class="main-nav" style="left:874px">Blog</span>
  </nav>
  <a class="btn" style="left:946px;top:32px;width:112px;height:34px">Contact Us</a>
</header>

<!-- Hero -->
<section class="hero">
  <div class="hero-bg" role="img" aria-label="Forest canopy under a bright blue sky"></div>
  <div class="photo hero-photo" role="img" aria-label="Arborist in safety gear climbing a tall trunk with a chainsaw"></div>
  <h1 class="hero-title">EXPERT TREE CARE<br>AND&nbsp; LANDSCAPING<br>SOLUTIONS FOR YOU</h1>
  <p class="hero-sub">Serving Lafayette &amp; Surrounding Areas.</p>
  <a class="btn" style="left:141px;top:326px;width:112px;height:34px">Contact Us</a>
  <svg class="hero-wave" width="1200" height="160" viewBox="0 0 1200 160">
    <path d="M0 211 L0 111 C250 160 520 180 720 150 C930 118 1100 80 1200 0 L1200 211 Z" fill="#f7a928"/>
    <path d="M0 211 L0 126 C250 175 520 200 720 170 C930 140 1100 100 1200 30 L1200 211 Z" fill="#fff"/>
  </svg>
</section>

<!-- Services -->
<h2 class="section-title" style="top:740px">OUR SERVICES</h2>
<svg class="ornament" style="left:560px;top:783px"><use href="#ornament"/></svg>
<p class="services-text">Lorem Ipsum is simply dummy text of the printing and typesetting industry. Lorem Ipsum has been the industry's standard dummy text ever since.</p>

<svg class="slider-arrow" style="left:84px" viewBox="0 0 36 36">
  <circle cx="18" cy="18" r="17" fill="#fff" stroke="#f7a928" stroke-width="1.5"/>
  <path d="M23 18H13M17 13l-5 5 5 5" fill="none" stroke="#f7a928" stroke-width="1.8"/>
</svg>
<svg class="slider-arrow" style="left:1080px" viewBox="0 0 36 36">
  <circle cx="18" cy="18" r="18" fill="#f7a928"/>
  <path d="M13 18h10M19 13l5 5-5 5" fill="none" stroke="#2c2c2c" stroke-width="1.8"/>
</svg>

<article class="service-card" style="left:141px">
  <div class="photo" role="img" aria-label="Gloved hands pruning a branch with shears" style="background:linear-gradient(160deg,#3f7a2a,#8fbf5a)"></div>
  <span class="service-icon"><svg width="24" height="24"><use href="#tree"/></svg></span>
  <h3 class="service-name" style="top:205px">Tree Pruning</h3>
</article>
<article class="service-card is-active" style="left:376px">
  <div class="photo" role="img" aria-label="Worker cutting a fallen log with a chainsaw" style="background:linear-gradient(160deg,#4c5d3a,#7f8c5a)"></div>
  <span class="service-icon"><svg width="24" height="24"><use href="#tree"/></svg></span>
  <h3 class="service-name" style="top:205px">Tree Removal</h3>
</article>
<article class="service-card" style="left:611px">
  <div class="photo" role="img" aria-label="Worker in a safety vest planting a seedling" style="background:linear-gradient(160deg,#3d4a3a,#8a6a3e)"></div>
  <span class="service-icon"><svg width="24" height="24"><use href="#tree"/></svg></span>
  <h3 class="service-name" style="top:205px">Tree Preservation</h3>
</article>
<article class="service-card" style="left:845px">
  <div class="photo" role="img" aria-label="Orange stump grinder working on a cut stump" style="background:linear-gradient(160deg,#6b8a3a,#c98a3a)"></div>
  <span class="service-icon"><svg width="24" height="24"><use href="#tree"/></svg></span>
  <h3 class="service-name" style="top:205px">Stump Grinding</h3>
</article>

<a class="btn" style="left:528px;top:1189px;width:142px;height:34px">View All Services</a>

<!-- About -->
<div class="photo about-photo" role="img" aria-label="Person starting a chainsaw beside a tree stump in a pine forest"></div>
<section class="info-panel" style="left:607px;top:1392px;width:451px;height:426px">
  <h2 class="panel-title" style="position:absolute;left:32px;top:40px">ABOUT VERDELL<br>TREE CARE</h2>
  <svg class="ornament" style="left:32px;top:125px;width:56px"><use href="#ornament"/></svg>
  <div class="about-copy">
    <p>At Verdell Tree Care, we are more than just a tree service company, we are stewards of our beautiful trees. With a passion deeply rooted in arboriculture, we embark on a mission to promote the health, beauty, and safety of your trees and landscapes.</p>
    <p>Whether it's expert tree trimming to enhance aesthetics, meticulous tree removal to mitigate hazards, or comprehensive tree health assessments to ensure safety, we approach each task with unwavering dedication and attention to detail.</p>
  </div>
  <a class="btn btn-orange" style="left:32px;top:342px;width:104px;height:34px">Contact Us</a>
</section>

<!-- Service area -->
<div class="photo area-map" role="img" aria-label="Aerial map of the service region with location pins"></div>
<h2 class="section-title" style="left:697px;width:auto;top:2038px;text-align:left;font-size:31px">SERVICE AREA</h2>
<svg class="ornament" style="left:697px;top:2083px;width:56px"><use href="#ornament"/></svg>
<ul class="area-list" style="list-style:none">
  <li class="area-item" style="left:697px;top:2121px"><svg width="14" height="18" style="color:#f7a928"><use href="#pin"/></svg>Carencro</li>
  <li class="area-item is-current" style="left:697px;top:2161px"><svg width="14" height="18" style="color:#7cc242"><use href="#pin"/></svg>Scott</li>
  <li class="area-item" style="left:697px;top:2200px"><svg width="14" height="18" style="color:#f7a928"><use href="#pin"/></svg>Judice</li>
  <li class="area-item" style="left:697px;top:2240px"><svg width="14" height="18" style="color:#f7a928"><use href="#pin"/></svg>Morgan City</li>
  <li class="area-item" style="left:697px;top:2279px"><svg width="14" height="18" style="color:#f7a928"><use href="#pin"/></svg>Denham Spring</li>
  <li class="area-item" style="left:867px;top:2121px"><svg width="14" height="18" style="color:#f7a928"><use href="#pin"/></svg>Duson</li>
  <li class="area-item" style="left:867px;top:2161px"><svg width="14" height="18" style="color:#f7a928"><use href="#pin"/></svg>Broussard</li>
  <li class="area-item" style="left:867px;top:2200px"><svg width="14" height="18" style="color:#f7a928"><use href="#pin"/></svg>Youngsville</li>
  <li class="area-item" style="left:867px;top:2240px"><svg width="14" height="18" style="color:#f7a928"><use href="#pin"/></svg>Shenandoah</li>
  <li class="area-item" style="left:867px;top:2279px"><svg width="14" height="18" style="color:#f7a928"><use href="#pin"/></svg>Lake Charles</li>
</ul>
<a class="btn" style="left:697px;top:2328px;width:105px;height:33px">Contact Us</a>

<!-- Why choose -->
<div class="photo why-photo" role="img" aria-label="Arborist cutting a high branch with a chainsaw against the sky"></div>
<section class="info-panel" style="left:141px;top:2592px;width:452px;height:351px">
  <h2 class="panel-title" style="position:absolute;left:24px;top:44px;font-size:29px">WHY CHOOSE US?</h2>
  <svg class="ornament" style="left:22px;top:88px;width:56px"><use href="#ornament"/></svg>
  <span class="why-item" style="left:24px;top:117px"><svg width="16" height="16"><use href="#tick"/></svg>Locally Owned &amp; Operated</span>
  <span class="why-item" style="left:24px;top:151px"><svg width="16" height="16"><use href="#tick"/></svg>Safety is Our No.1 Priority</span>
  <span class="why-item" style="left:24px;top:185px"><svg width="16" height="16"><use href="#tick"/></svg>Licensed Arborist on Staff</span>
  <span class="why-item" style="left:24px;top:219px"><svg width="16" height="16"><use href="#tick"/></svg>24-Hours Emergency Services</span>
  <span class="why-item" style="left:267px;top:117px"><svg width="16" height="16"><use href="#tick"/></svg>Licensed &amp; Insured</span>
  <span class="why-item" style="left:267px;top:151px"><svg width="16" height="16"><use href="#tick"/></svg>Professional Work</span>
  <span class="why-item" style="left:267px;top:185px"><svg width="16" height="16"><use href="#tick"/></svg>Free Estimates</span>
  <a class="btn btn-orange" style="left:22px;top:263px;width:129px;height:39px;font-size:14px">Contact Us</a>
</section>

<!-- Blog -->
<h2 class="section-title" style="top:3110px">LATEST BLOG POSTS</h2>
<svg class="ornament" style="left:560px;top:3154px"><use href="#ornament"/></svg>

<article class="blog-card" style="left:141px">
  <div class="photo" role="img" aria-label="Felled trees lying in a cleared forest yard" style="background:linear-gradient(160deg,#5d7a45,#9aa56a)"></div>
  <h3>Dolor Sit Amet Lorem Ipsum Situm Ctetuer Conse Adipis.</h3>
  <p>Lorem ipsum dolor sit amet consectetuer adipiscing elit, sed diam nonummy nibh euismod tincidunt ut laoreet...</p>
  <span class="date" style="left:14px;top:335px"><svg width="14" height="14"><use href="#calendar"/></svg>12.06.2024</span>
</article>
<article class="blog-card" style="left:439px">
  <div class="photo" role="img" aria-label="Arborist roped into a tree cutting branches" style="background:linear-gradient(160deg,#4f6e3a,#a2b07a)"></div>
  <h3>Lorem Ipsum SitumDolor Sit Amet Ctetuer Conse Adipis.</h3>
  <p>Lorem ipsum dolor sit amet consectetuer adipiscing elit, sed diam nonummy nibh euismod tincidunt ut laoreet...</p>
  <span class="date" style="left:14px;top:335px"><svg width="14" height="14"><use href="#calendar"/></svg>11.06.2024</span>
</article>

<article class="blog-mini" style="top:3197px">
  <div class="photo" role="img" aria-label="Crew sawing a fallen trunk" style="background:linear-gradient(160deg,#6b7a5a,#b08a5a)"></div>
  <h4>Lorem Ipsum Situ Dolor Sit Amet Ctetuer Conse Adipis Ipsum .</h4>
  <span class="date"><svg width="14" height="14"><use href="#calendar"/></svg>11.06.2024</span>
</article>
<article class="blog-mini" style="top:3338px">
  <div class="photo" role="img" aria-label="Arborist cutting a high limb" style="background:linear-gradient(160deg,#9ab0c0,#6b7a5a)"></div>
  <h4>Lore Ipsum Situm Dolor Sit Amet Ctetuer Conse Adipis Ipsum .</h4>
  <span class="date"><svg width="14" height="14"><use href="#calendar"/></svg>10.06.2024</span>
</article>
<article class="blog-mini" style="top:3480px">
  <div class="photo" role="img" aria-label="Chainsaw cutting into a log" style="background:linear-gradient(160deg,#5a5a3a,#c9a04a)"></div>
  <h4>Lore Ipsum Situm Dolor Sit Amet Ctetuer Conse Adipis Ipsum .</h4>
  <span class="date"><svg width="14" height="14"><use href="#calendar"/></svg>20.08.2015</span>
</article>

<a class="btn" style="left:535px;top:3595px;width:128px;height:34px">View All Blogs</a>

<!-- Quick inquiry -->
<div class="photo inquiry-photo" role="img" aria-label="Looking up through a green forest canopy"></div>
<h2 class="section-title" style="top:3795px;color:var(--white)">QUICK INQUIRY</h2>
<svg class="ornament" style="left:560px;top:3839px"><use href="#ornament"/></svg>
<form>
  <div class="field" style="left:274px;top:3874px;width:317px;height:39px">Full Name<sup>*</sup></div>
  <div class="field" style="left:607px;top:3874px;width:317px;height:39px">Phone<sup>*</sup></div>
  <div class="field" style="left:274px;top:3928px;width:317px;height:39px">E-Mail<sup>*</sup></div>
  <div class="field" style="left:607px;top:3928px;width:317px;height:39px">Inquiry For<sup>*</sup>
    <svg width="10" height="7" style="position:absolute;right:14px;top:17px"><path d="M1 1l4 4 4-4" fill="none" stroke="#2c2c2c" stroke-width="1.5"/></svg>
  </div>
  <div class="field" style="left:274px;top:3981px;width:650px;height:153px">Message</div>
  <a class="btn btn-orange" style="left:543px;top:4159px;width:113px;height:34px">Submit Now</a>
</form>

<!-- Footer -->
<footer class="site-footer">
  <div class="footer-brand">
    <span class="brand-mark"></span>
    <span class="brand-name">VERDELL<br>TREE CARE</span>
  </div>
  <span class="social" style="left:192px" aria-label="Social profile"></span>
  <span class="social" style="left:235px" aria-label="Social profile"></span>
  <span class="social" style="left:279px" aria-label="Social profile"></span>
  <span class="social" style="left:322px" aria-label="Social profile"></span>

  <h3 class="footer-heading" style="left:582px">Quick Links</h3>
  <span class="footer-link" style="top:88px">• Home</span>
  <span class="footer-link" style="top:120px">• About Us</span>
  <span class="footer-link" style="top:153px">• Services</span>
  <span class="footer-link" style="top:185px">• Blog</span>
  <span class="footer-link" style="top:219px">• Contact Us</span>

  <h3 class="footer-heading" style="left:863px">Contact Details</h3>
  <div class="contact-row" style="top:85px">
    <svg width="30" height="30" viewBox="0 0 30 30"><path d="M15 3c-5 0-9 4-9 9 0 6 9 14 9 14s9-8 9-14c0-5-4-9-9-9z" fill="none" stroke="#fff" stroke-width="1.5"/><circle cx="15" cy="12" r="3.5" fill="none" stroke="#fff" stroke-width="1.5"/></svg>
    <span>48 Orchard Row,<br>Lafayette, Louisiana.</span>
  </div>
  <div class="contact-row" style="top:150px">
    <svg width="30" height="30" viewBox="0 0 30 30"><path d="M8 4l5 5-3 3c1.5 3.5 4.5 6.5 8 8l3-3 5 5-3 4C13 25 5 17 4 7z" fill="none" stroke="#fff" stroke-width="1.5"/></svg>
    <span>(555) 014-2739<br>(555) 013-9939</span>
  </div>
  <div class="contact-row" style="top:206px">
    <svg width="30" height="30" viewBox="0 0 30 30"><rect x="4" y="8" width="22" height="16" fill="none" stroke="#fff" stroke-width="1.5"/><path d="M4 8l11 9 11-9" fill="none" stroke="#fff" stroke-width="1.5"/></svg>
    <span>E-Mail<br>info@verdelltreecare.com</span>
  </div>

  <div class="footer-rule"></div>
  <p class="copyright">© 2024 Verdell Tree Care. All Rights Reserved.</p>
</footer>

</body>
</html>
```